Copper Lantern

Need a business card for our restaurant. Restaurant and Bar in the mountains of North Idaho. Rustic looking card

rustic design, wood and metal looking, primarily neutral colors

• Name, address, phone number, website, email address

```html
<!DOCTYPE html>
<html lang="en">
<head>
<meta charset="utf-8">
<title>Copper Lantern – Business Card</title>
<link href="https://fonts.googleapis.com/css2?family=Lato:wght@400;700&display=swap" rel="stylesheet">
<style>
  :root {
    --backdrop: #6b6b6b;
    --card: #1c1c1c;
    --card-deep: #0d0d0d;
    --sheen: #4a4a4a;
    --sheen-soft: #2e2e2e;
    --ink: #ffffff;
    --badge: #ffffff;
    --badge-ink: #1c1c1c;
  }
  * { margin: 0; padding: 0; box-sizing: border-box; }
  html, body { width: 1200px; height: 900px; overflow: hidden; }
  body {
    background: var(--backdrop);
    font-family: "Lato", sans-serif;
    color: var(--ink);
    display: flex;
    flex-direction: column;
    align-items: center;
    justify-content: center;
    gap: 40px;
  }
  .card {
    width: 680px;
    height: 389px;
    border-radius: 26px;
    background: var(--card);
    position: relative;
    overflow: hidden;
    box-shadow: 0 10px 30px rgba(0,0,0,0.35);
  }
  .card-front .pattern-area {
    position: absolute; inset: 0;
    background:
      radial-gradient(ellipse 55% 45% at 78% 18%, var(--sheen), transparent 70%),
      radial-gradient(ellipse 45% 40% at 22% 80%, var(--sheen-soft), transparent 70%),
      linear-gradient(160deg, #262626 0%, var(--card-deep) 55%, #1f1f1f 100%);
  }
  .card-front .front-name {
    position: absolute;
    left: 0; right: 0; top: 150px;
    text-align: center;
    font-size: 24px;
    font-weight: 700;
    letter-spacing: 1px;
  }
  .badge {
    position: absolute;
    left: 70px; top: 84px;
    width: 220px; height: 220px;
    border-radius: 50%;
    background: var(--badge);
    display: flex; align-items: center; justify-content: center;
    text-align: center;
  }
  .badge-name {
    color: var(--badge-ink);
    font-size: 26px;
    font-weight: 700;
    line-height: 1.2;
    letter-spacing: 1px;
  }
  .divider {
    position: absolute;
    left: 340px; top: 60px;
    width: 2px; height: 270px;
    background: linear-gradient(to bottom, transparent, #ffffff 50%, transparent);
  }
  .details {
    position: absolute;
    left: 372px; top: 62px;
  }
  .person-name { font-size: 34px; font-weight: 700; }
  .person-role { font-size: 20px; margin-top: 6px; }
  .address { font-size: 21px; line-height: 1.3; margin-top: 22px; }
  .contacts { list-style: none; margin-top: 20px; font-size: 21px; }
  .contacts li { display: flex; align-items: center; gap: 12px; line-height: 1.45; }
  .contacts svg { width: 18px; height: 18px; fill: var(--ink); flex-shrink: 0; }
</style>
</head>
<body>
  <section class="card card-front">
    <div class="pattern-area" role="img" aria-label="Embossed repeating brand pattern, glossy black on matte black"></div>
    <div class="front-name">Copper Lantern</div>
  </section>

  <section class="card card-back">
    <div class="badge">
      <span class="badge-name">Copper<br>Lantern</span>
    </div>
    <div class="divider"></div>
    <div class="details">
      <h1 class="person-name">Jonathan Smith</h1>
      <p class="person-role">Owner</p>
      <p class="address">421, Address line goes here<br>45452, Country name</p>
      <ul class="contacts">
        <li>
          <svg viewBox="0 0 24 24" aria-hidden="true"><path d="M6.6 10.8a15.1 15.1 0 0 0 6.6 6.6l2.2-2.2a1 1 0 0 1 1-.25 11.4 11.4 0 0 0 3.6.57 1 1 0 0 1 1 1V20a1 1 0 0 1-1 1A17 17 0 0 1 3 4a1 1 0 0 1 1-1h3.5a1 1 0 0 1 1 1 11.4 11.4 0 0 0 .57 3.6 1 1 0 0 1-.25 1z"/></svg>
          123.456.7890
        </li>
        <li>
          <svg viewBox="0 0 24 24" aria-hidden="true"><path d="M2 5h20v14H2z M4 7v.4l8 5.2 8-5.2V7z" fill-rule="evenodd"/></svg>
          info@webname.com
        </li>
        <li>
          <svg viewBox="0 0 24 24" aria-hidden="true"><circle cx="12" cy="12" r="10"/><path d="M2 12h20M12 2c3 3 3 17 0 20M12 2c-3 3-3 17 0 20" stroke="#1c1c1c" stroke-width="1.5" fill="none"/></svg>
          www.website.com
        </li>
      </ul>
    </div>
  </section>
</body>
</html>
```